Website homepage rework for women's travel website

I have a homepage (http://www.ladies-at-the-helm.com) that I'm 50% happy with but don't want to completely overhaul. I'd like to retain a similar look but upgrade it to something a bit more modern and less old-fashioned. The basic sense of the site is empowering, self-confident, fun and adventurous - but female and over 40.

A number of the elements on the page have to be redesigned, a few can be tweaked, and a few left alone. See the rest of the brief for further information.

Target Market(s)

women over 40 who like to travel

Industry/Entity Type

Travel

Number of Pages Required

1 page

Font styles to use
Other font styles liked:
• see my brief

Requirements
Must have
• - size - the page must be significantly wider
• - the only font I MUST keep is Raleway (as in the tagline) and possibly the font of the site name (Ladies at the Helm). Both of those work for me. There are too many fonts on the page, however, and that needs to be unified.
• - the rectangles I click to get inside the site have to change to something more modern, possibly square - they do not have to be separated into two columns as they are now, nor do they need the titles (toolkit etc)
• - I like the background image of the header - but it needs to be wider of course - also keep in mind the aspect - it has to fit into the smaller inside pages, whose size will not change
• - at the end of the project I need to receive the separate elements of the design so I can eventually make a change myself if needed ie. replace my own photo, for example
Nice to have
• - the three photos need to change to something more eye-popping - or something else should take their place to fill the space
Should not have
• I do not want a full, original redesign. I want my readers to still feel as though they are on the same site - same header, mostly same fonts.

```html
<!DOCTYPE html>
<html lang="en">
<head>
<meta charset="utf-8">
<title>Ladies at the Helm — For women who travel smart, safe + solo</title>
<link rel="stylesheet" href="https://fonts.googleapis.com/css2?family=Raleway:wght@400;500;600;700&family=Open+Sans:wght@400;600&family=Oswald:wght@500;600&display=swap">
<style>
:root{
  --page-bg:#f6f6f6;
  --header-bg:#f3f3f3;
  --ink:#1d1d1d;
  --ink-soft:#555;
  --muted:#8a8a8a;
  --rule:#d9d9d9;
  --brand-orange:#e8551c;
  --brand-yellow:#fecb2f;
  --brand-red:#d8262d;
  --band-blue:#0a6fd1;
  --card-grey:#e6e6e6;
  --footer-navy:#1d2a44;
  --white:#ffffff;
}
*{box-sizing:border-box;margin:0;padding:0}
html,body{width:1200px;height:2521px;overflow:hidden}
body{position:relative;background:var(--page-bg);font-family:"Raleway",sans-serif;color:var(--ink)}
.abs{position:absolute}

/* Header */
.site-header{left:0;top:0;width:1200px;height:119px;background:var(--header-bg)}
.brand{left:96px;top:26px}
.brand-name{font-family:"Raleway",sans-serif;font-weight:700;font-size:38px;line-height:44px;color:var(--brand-orange);letter-spacing:.3px}
.brand-tagline{font-size:20px;color:#333;margin-top:2px}
.main-nav{left:543px;top:0;height:92px;display:flex;align-items:stretch;font-size:11.5px;font-weight:600;letter-spacing:.4px;text-transform:uppercase}
.main-nav a{display:flex;align-items:center;padding:8px 11px 0;color:#333;text-decoration:none}
.main-nav a.is-active{background:var(--brand-yellow);width:104px;justify-content:center;padding:8px 0 0;margin-right:2px}

/* Hero */
.hero{left:0;top:119px;width:1200px;height:469px;
  background:linear-gradient(180deg,#f6b42a 0%,#f09a22 35%,#d88a3c 60%,#a98a66 85%,#8c7b66 100%)}

/* Intro */
.intro-title{left:0;top:633px;width:1200px;text-align:center;font-size:25px;font-weight:600}
.feature-card{width:254px;height:244px;top:723px;background:var(--card-grey);border:1px solid #dcdcdc;text-align:center}
.feature-card svg{position:absolute;left:79px;top:22px}
.feature-card h3{position:absolute;top:132px;width:100%;font-size:19px;font-weight:600}
.feature-card p{position:absolute;top:168px;left:22px;right:22px;font-family:"Open Sans",sans-serif;font-size:12.5px;line-height:19px;color:#888}

/* Call to action band */
.cta-band{left:0;top:1061px;width:1200px;height:151px;background:linear-gradient(90deg,#0b66c4,#0d76da 50%,#0a6bcc)}
.cta-text{left:141px;top:1118px;font-size:27px;color:var(--white)}
.cta-button{left:832px;top:1113px;width:197px;height:50px;background:var(--brand-yellow);color:#222;font-size:22px;display:flex;align-items:center;justify-content:center;border-radius:2px}

/* Topic tiles */
.topics{left:0;top:1212px;width:1200px;height:314px;background:#efefef}
.topic-tile{width:278px;height:80px;overflow:hidden}
.topic-tile .label{position:absolute;left:0;top:0;width:100%;height:46px;padding:4px 12px}
.topic-tile .label b{display:block;font-family:"Oswald",sans-serif;font-weight:600;font-size:21px;line-height:24px;color:var(--white);text-transform:uppercase}
.topic-tile .label span{display:block;font-family:"Raleway",sans-serif;font-size:14px;line-height:16px;color:rgba(255,255,255,.92)}
.topic-tile .photo{position:absolute;left:0;top:46px;width:100%;height:34px}

/* Latest blog */
.blog-heading{left:0;top:1576px;width:1200px;text-align:center;font-size:25px;font-weight:600}
.post{width:283px;top:1647px}
.post .thumb{width:283px;height:187px}
.post h4{margin:18px 10px 0;font-size:13px;font-weight:600;line-height:18px;height:40px}
.post p{margin:8px 10px 0;font-family:"Open Sans",sans-serif;font-size:10.5px;line-height:17.5px;color:#999}
.post .meta{margin:10px 10px 0;border-top:1px solid var(--rule);border-bottom:1px solid var(--rule);height:33px;display:flex;align-items:center;gap:26px;font-family:"Open Sans",sans-serif;font-size:9.5px;color:#666;text-transform:uppercase}
.post .meta span{display:flex;align-items:center;gap:6px}

/* Newsletter */
.newsletter{left:0;top:2071px;width:1200px;height:119px;background:var(--brand-yellow)}
.newsletter-title{left:144px;top:2107px;border-left:3px solid #444;padding-left:7px}
.newsletter-title strong{display:block;font-size:19px;font-weight:500;color:#333}
.newsletter-title em{display:block;font-family:"Open Sans",sans-serif;font-size:10px;color:#555;font-style:italic;margin-top:3px}
.email-field{left:459px;top:2115px;width:402px;height:33px;background:var(--white);border-radius:3px;font-family:"Open Sans",sans-serif;font-size:12px;color:#aaa;padding:9px 17px}
.subscribe-btn{left:877px;top:2115px;width:113px;height:33px;background:var(--brand-red);color:var(--white);font-size:12px;font-weight:600;display:flex;align-items:center;justify-content:center;border-radius:2px}

/* Footer */
.site-footer{left:0;top:2190px;width:1200px;height:331px;background:linear-gradient(180deg,#2c3a55 0%,#1d2a44 55%,#3b3a4a 85%,#6a4a3a 100%)}
.footer-brand{left:0;top:2258px;width:1200px;text-align:center}
.footer-brand .brand-name{font-size:42px;line-height:48px;color:var(--brand-orange)}
.footer-brand .brand-tagline{font-size:22px;color:var(--white);margin-top:4px}
.copyright{left:0;top:2382px;width:1200px;text-align:center;font-size:10px;font-weight:600;color:var(--white);letter-spacing:.3px}
.social{left:481px;top:2445px;display:flex;gap:9px}
.social span{width:36px;height:36px;display:block}
</style>
</head>
<body>

<header class="site-header abs">
  <div class="brand abs">
    <div class="brand-name">Ladies at the Helm</div>
    <div class="brand-tagline">For women who travel smart, safe + solo</div>
  </div>
  <nav class="main-nav abs">
    <a class="is-active" href="#">Start Here</a>
    <a href="#">About</a>
    <a href="#">Travel Resources</a>
    <a href="#">Blog</a>
    <a href="#">Travel Shop</a>
    <a href="#">Contact</a>
  </nav>
</header>

<section class="hero abs" role="img" aria-label="Header photo: sunlit desert road with three pinned travel snapshots and a portrait of the site author"></section>

<h1 class="intro-title abs">Hi, I'm Mara. I took my first solo trip at 15. I'll show you how to travel...</h1>

<article class="feature-card abs" style="left:180px">
  <svg width="96" height="96" viewBox="0 0 96 96" aria-hidden="true">
    <circle cx="48" cy="48" r="48" fill="#f2c04a"/>
    <rect x="40" y="18" width="16" height="10" rx="3" fill="none" stroke="#333" stroke-width="3"/>
    <rect x="28" y="27" width="40" height="46" rx="6" fill="#e23a3a"/>
    <path d="M40 50l16-6-5 8 3 4-4-2-4 4z" fill="#fff"/>
    <circle cx="36" cy="77" r="3" fill="#333"/><circle cx="60" cy="77" r="3" fill="#333"/>
  </svg>
  <h3>Smart</h3>
  <p>Practical tools to help you plan – and afford – the perfect trip</p>
</article>

<article class="feature-card abs" style="left:472px">
  <svg width="96" height="96" viewBox="0 0 96 96" aria-hidden="true">
    <circle cx="48" cy="48" r="48" fill="#2f3f70"/>
    <path d="M48 22l20 8v16c0 14-9 23-20 28-11-5-20-14-20-28V30z" fill="#fff"/>
    <path d="M39 48l7 7 13-14" fill="none" stroke="#2f3f70" stroke-width="5" stroke-linecap="round" stroke-linejoin="round"/>
  </svg>
  <h3>Safe</h3>
  <p>Down-to-earth advice and a ton of safety recommendations</p>
</article>

<article class="feature-card abs" style="left:765px">
  <svg width="96" height="96" viewBox="0 0 96 96" aria-hidden="true">
    <circle cx="48" cy="48" r="48" fill="#a8e6be"/>
    <ellipse cx="48" cy="56" rx="30" ry="9" fill="#f0b431"/>
    <path d="M34 55c0-12 6-18 14-18s14 6 14 18z" fill="#f5c445"/>
    <path d="M34 52h28" stroke="#e0583a" stroke-width="4"/>
  </svg>
  <h3>Solo</h3>
  <p>Yes, you can do it!</p>
</article>

<section class="cta-band abs"></section>
<p class="cta-text abs">Thinking of solo travel?&nbsp; Click here to find out how.</p>
<a class="cta-button abs">Read More</a>

<section class="topics abs"></section>

<div class="topic-tile abs" style="left:141px;top:1256px">
  <div class="label" style="background:linear-gradient(90deg,#e23d1c,#f26b1d)"><b>Eating with Locals</b><span>The ultimate guide to social dining</span></div>
  <div class="photo" role="img" aria-label="Shared dinner table with plates of food" style="background:linear-gradient(90deg,#c96a3b,#e8b07a,#8a4a2e)"></div>
</div>
<div class="topic-tile abs" style="left:447px;top:1256px">
  <div class="label" style="background:linear-gradient(90deg,#d06a1c,#e8841e)"><b>No Single Supplement</b><span>17 ways to avoid paying it</span></div>
  <div class="photo" role="img" aria-label="Sunset over an open landscape" style="background:linear-gradient(90deg,#7a3a16,#e08a2c,#4a2a18)"></div>
</div>
<div class="topic-tile abs" style="left:753px;top:1256px">
  <div class="label" style="background:linear-gradient(90deg,#7d3fa0,#a45bc0)"><b>Your Packing List</b><span>Take what you need - no more</span></div>
  <div class="photo" role="img" aria-label="Packed travel bag and shoes" style="background:linear-gradient(90deg,#7a5a8a,#b6525a,#6a4a6a)"></div>
</div>

<div class="topic-tile abs" style="left:141px;top:1394px">
  <div class="label" style="background:linear-gradient(90deg,#f0c419,#f6d33a)"><b>Solo in Argentina</b><span>Does it really take two to tango?</span></div>
  <div class="photo" role="img" aria-label="Colourful street scene" style="background:linear-gradient(90deg,#2fb5c8,#e9a03c,#3aa0c0)"></div>
</div>
<div class="topic-tile abs" style="left:447px;top:1394px">
  <div class="label" style="background:linear-gradient(90deg,#2cc4bd,#48d4c6)"><b>Europe for Foodies</b><span>9 top destinations to try in October</span></div>
  <div class="photo" role="img" aria-label="Close-up of saffron rice" style="background:linear-gradient(90deg,#e8c233,#f2d75a,#d9b02a)"></div>
</div>
<div class="topic-tile abs" style="left:753px;top:1394px">
  <div class="label" style="background:linear-gradient(90deg,#c8161d,#de2a2a)"><b>Solo Female Travel</b><span>A 3-week Central Asia itinerary</span></div>
  <div class="photo" role="img" aria-label="Route map of Central Asia" style="background:linear-gradient(90deg,#e8dcc4,#d9c8a8,#c8d4dc)"></div>
</div>

<h2 class="blog-heading abs">Latest Blog</h2>

<article class="post abs" style="left:146px">
  <div class="thumb" role="img" aria-label="Plate of seafood paella with prawns" style="background:linear-gradient(160deg,#e8b13a,#d98a2a 50%,#5a2a1a)"></div>
  <h4>My 9 European Foodie Destinations for October</h4>
  <p>Returning home after spending September in Central Asia, I was shocked. I'd left in summer, yet some of my trees were bare, and the rake was waiting for my swift hand...</p>
  <div class="meta">
    <span><svg width="16" height="14" viewBox="0 0 16 14" aria-hidden="true"><path d="M2 1h12v8H7l-4 3V9H2z" fill="none" stroke="#666" stroke-width="1.3"/></svg>16 Comments</span>
    <span><svg width="13" height="12" viewBox="0 0 13 12" aria-hidden="true"><path d="M6.5 11L1.5 6A2.8 2.8 0 0 1 6.5 2 2.8 2.8 0 0 1 11.5 6z" fill="none" stroke="#666" stroke-width="1.3"/></svg>98 Likes</span>
  </div>
</article>

<article class="post abs" style="left:456px">
  <div class="thumb" role="img" aria-label="Tiled turquoise minaret against a blue sky" style="background:linear-gradient(90deg,#1f5bd0 0%,#2a6fe0 25%,#5ab0b0 40%,#b8a888 55%,#4aa0a8 70%,#2a6fe0 85%)"></div>
  <h4>A Solo Woman's 3-Week Central Asia Itinerary</h4>
  <p>Returning home after spending September in Central Asia, I was shocked. I'd left in summer, yet some of my trees were bare, and the rake was waiting for my swift hand...</p>
  <div class="meta">
    <span><svg width="16" height="14" viewBox="0 0 16 14" aria-hidden="true"><path d="M2 1h12v8H7l-4 3V9H2z" fill="none" stroke="#666" stroke-width="1.3"/></svg>16 Comments</span>
    <span><svg width="13" height="12" viewBox="0 0 13 12" aria-hidden="true"><path d="M6.5 11L1.5 6A2.8 2.8 0 0 1 6.5 2 2.8 2.8 0 0 1 11.5 6z" fill="none" stroke="#666" stroke-width="1.3"/></svg>98 Likes</span>
  </div>
</article>

<article class="post abs" style="left:765px">
  <div class="thumb" role="img" aria-label="Old bakery shopfront with wooden doors" style="background:linear-gradient(90deg,#5a3a22,#9a6a44 40%,#c2543a 70%,#4a2e1e)"></div>
  <h4>Carouge, Geneva's Alter Ego?</h4>
  <p>Returning home after spending September in Central Asia, I was shocked. I'd left in summer, yet some of my trees were bare, and the rake was waiting for my swift hand...</p>
  <div class="meta">
    <span><svg width="16" height="14" viewBox="0 0 16 14" aria-hidden="true"><path d="M2 1h12v8H7l-4 3V9H2z" fill="none" stroke="#666" stroke-width="1.3"/></svg>16 Comments</span>
    <span><svg width="13" height="12" viewBox="0 0 13 12" aria-hidden="true"><path d="M6.5 11L1.5 6A2.8 2.8 0 0 1 6.5 2 2.8 2.8 0 0 1 11.5 6z" fill="none" stroke="#666" stroke-width="1.3"/></svg>98 Likes</span>
  </div>
</article>

<section class="newsletter abs"></section>
<div class="newsletter-title abs">
  <strong>SUBSCRIPTION NEWSLETTER</strong>
  <em>Keep yourself updated for our latest updates</em>
</div>
<div class="email-field abs">Enter email address</div>
<div class="subscribe-btn abs">SUBSCRIBE</div>

<footer class="site-footer abs" role="img" aria-label="City street at dusk with light trails from traffic"></footer>
<div class="footer-brand abs">
  <div class="brand-name">Ladies at the Helm</div>
  <div class="brand-tagline">For women who travel smart, safe + solo</div>
</div>
<p class="copyright abs">© 2016 COPYRIGHTS. ALL RIGHT RESERVED.</p>
<div class="social abs" aria-label="Social links">
  <span><svg width="36" height="36" viewBox="0 0 36 36" aria-hidden="true"><rect x="7" y="7" width="22" height="22" transform="rotate(45 18 18)" fill="none" stroke="#f0c419" stroke-width="1.5"/><circle cx="18" cy="18" r="4" fill="#f0c419"/></svg></span>
  <span><svg width="36" height="36" viewBox="0 0 36 36" aria-hidden="true"><rect x="7" y="7" width="22" height="22" transform="rotate(45 18 18)" fill="none" stroke="#f0c419" stroke-width="1.5"/><circle cx="18" cy="18" r="4" fill="#f0c419"/></svg></span>
  <span><svg width="36" height="36" viewBox="0 0 36 36" aria-hidden="true"><rect x="7" y="7" width="22" height="22" transform="rotate(45 18 18)" fill="none" stroke="#f0c419" stroke-width="1.5"/><circle cx="18" cy="18" r="4" fill="#f0c419"/></svg></span>
  <span><svg width="36" height="36" viewBox="0 0 36 36" aria-hidden="true"><rect x="7" y="7" width="22" height="22" transform="rotate(45 18 18)" fill="none" stroke="#f0c419" stroke-width="1.5"/><circle cx="18" cy="18" r="4" fill="#f0c419"/></svg></span>
</div>

</body>
</html>
```